Business Card for premium dental clinic

We are a premium dental clinic based in Brasov, Romania with more than 15 year on the market, providing quality dental treatment made by a team of more specialized dentists, working with modern equipment as a solution to beautiful and healthy teeth.

Our current logo for the clinic use 2 square with colors black and gold - dr Ternisu - studio, using family fonts Bodoni, Myriad Pro and Segoe Print.
Depending on the printing we used some gold CMYK background or gold foil picture background or a gold gradient.
We want a business card:
- eye catching business card
- distinguished business card
- premium design
- to keep the color scheme of black and gold
- to attract the customers to spent time reading the information
- modern concept

```html
<!DOCTYPE html>
<html lang="ro">
<head>
<meta charset="utf-8">
<title>dr Ternisu studio – business card</title>
<link href="https://fonts.googleapis.com/css2?family=Montserrat:wght@400;500;600&display=swap" rel="stylesheet">
<style>
  :root {
    --backdrop: #6f7173;
    --card-dark: #2a2c2e;
    --card-white: #ffffff;
    --gold: #c9a227;
    --text-light: #f2f2f2;
    --ink: #1b1b1b;
  }
  * { margin: 0; padding: 0; box-sizing: border-box; }
  html, body { width: 1200px; height: 866px; overflow: hidden; }
  body {
    background: var(--backdrop);
    font-family: "Montserrat", Arial, sans-serif;
    position: relative;
  }
  .card {
    position: absolute;
    width: 600px;
    height: 343px;
    border-radius: 4px;
    overflow: hidden;
    background: var(--card-dark);
    box-shadow: 0 10px 30px rgba(0,0,0,.35);
  }
  .card--back { left: 300px; top: 52px; }
  .card--front { left: 300px; top: 463px; }

  .brand {
    position: absolute;
    display: flex;
    align-items: center;
    gap: 14px;
    font-weight: 500;
    font-size: 30px;
    letter-spacing: .5px;
    white-space: nowrap;
  }
  .brand__square { width: 34px; height: 34px; background: var(--gold); flex: none; }
  .card--back .brand { left: 50%; top: 118px; transform: translateX(-50%); color: var(--text-light); }
  .card--front .brand { left: 50%; top: 58px; transform: translateX(-50%); color: var(--ink); }

  .address {
    position: absolute;
    left: 0; right: 0; top: 232px;
    text-align: center;
    color: var(--text-light);
    font-size: 14px;
    letter-spacing: .4px;
  }

  .front-shapes { position: absolute; inset: 0; width: 600px; height: 343px; }

  .person {
    position: absolute;
    right: 44px;
    top: 222px;
    text-align: left;
  }
  .person__name { color: var(--gold); font-weight: 600; font-size: 19px; letter-spacing: 1px; text-transform: uppercase; line-height: 24px; }
  .person__role { color: var(--text-light); font-size: 15px; line-height: 20px; }

  .contacts {
    position: absolute;
    left: 44px;
    bottom: 26px;
    list-style: none;
  }
  .contacts li {
    display: flex;
    align-items: center;
    gap: 12px;
    color: var(--text-light);
    font-size: 13px;
    letter-spacing: .3px;
    line-height: 24px;
  }
  .contacts svg { width: 14px; height: 14px; fill: var(--gold); flex: none; }
</style>
</head>
<body>

<section class="card card--back" aria-label="Card back">
  <div class="brand"><span class="brand__square"></span><span>dr Ternisu studio</span></div>
  <p class="address">Strada Lalelelor nr 7, 500210 Brașov</p>
</section>

<section class="card card--front" aria-label="Card front">
  <svg class="front-shapes" viewBox="0 0 600 343" aria-hidden="true">
    <path d="M0 0 H600 V20 C540 150 300 210 0 168 Z" fill="var(--card-white)"/>
    <path d="M0 168 C300 210 540 150 600 20 V58 C540 190 300 245 0 205 Z" fill="var(--gold)"/>
  </svg>

  <div class="brand"><span class="brand__square"></span><span>dr Ternisu studio</span></div>

  <div class="person">
    <p class="person__name">Mara Iliescu</p>
    <p class="person__role">Doctor</p>
  </div>

  <ul class="contacts">
    <li>
      <svg viewBox="0 0 24 24"><path d="M6.6 10.8a15.1 15.1 0 0 0 6.6 6.6l2.2-2.2a1 1 0 0 1 1-.25 11.4 11.4 0 0 0 3.6.57 1 1 0 0 1 1 1V20a1 1 0 0 1-1 1A17 17 0 0 1 3 4a1 1 0 0 1 1-1h3.5a1 1 0 0 1 1 1c0 1.25.2 2.45.57 3.57a1 1 0 0 1-.25 1z"/></svg>
      +40 268 555 019
    </li>
    <li>
      <svg viewBox="0 0 24 24"><path d="M2 5h20v14H2z M3.5 6.5 12 13l8.5-6.5" fill="none" stroke="var(--gold)" stroke-width="2"/></svg>
      m.iliescu@drternisu.ro
    </li>
    <li>
      <svg viewBox="0 0 24 24"><circle cx="12" cy="12" r="9" fill="none" stroke="var(--gold)" stroke-width="2"/><path d="M3 12h18M12 3c3 3 3 15 0 18M12 3c-3 3-3 15 0 18" fill="none" stroke="var(--gold)" stroke-width="1.6"/></svg>
      www.drternisu.ro
    </li>
  </ul>
</section>

</body>
</html>
```